Community-based social network needs a new landing page

We need a landing page for a local social network in Singapore called "LaneKindred.sg". It is a website that help neighbours to connect with each other for mutual benefits such as providing professional/non-professional services, sharing items, and neighbourly help, etc.

There is an existing website but we want to completely revamp it. It is most important that the new landing page communicates that the neighbourhood has skills and services for people to discover.

The final design of the landing page should be modern, and communicates a sense of community and vibrancy. As a matter of priority, more real estate should be accorded to the neighbours providing services elements.

We have drafted 2 reference sites that communicates the key ideas/user propositions for your easy reference:
http://tarvelquin8.example-sites.com/lanekindred
http://tarvelquin8.example-sites.com/lanekindred2

As long as the key ideas/user propositions are kept to, we are open to any design proposals. I.e. you do not have to follow the design layout of the reference sites

Target Market(s)

Our target market is primarily the Singapore community, includes all genders, education levels and occupations, aged between 17-45 years old.

In the file uploaded, you will find pictures of Singapore neighbourhoods and people of local ethnicities. Please use them, but you may arrange and add further filters to better enhance them

Industry/Entity Type

Real Estate

Requirements
Nice to have
• Landing page could be similar to that of www.gatherloft.com, not just at the top, but also the way the other categories are presented at the bottom.

```html
<!DOCTYPE html>
<html lang="en">
<head>
<meta charset="utf-8">
<title>LaneKindred.sg — Neighbourhood services and items pool</title>
<link href="https://fonts.googleapis.com/css2?family=Ubuntu:wght@300;400;500;700&family=Rokkitt:wght@400;500&display=swap" rel="stylesheet">
<style>
:root{
  --ink:#333;
  --muted:#8a8a8a;
  --header:#e6e6e6;
  --page:#f3f3f3;
  --band:#ececec;
  --blue:#3f7fc8;
  --blue-card:rgba(52,120,200,.92);
  --red-card:rgba(220,70,85,.92);
  --red:#d9150f;
  --cyan:#2bb6e8;
  --rule:#d0d0d0;
  --footer:#2b2b2b;
  --footer-text:#d6d6d6;
}
*{box-sizing:border-box;margin:0;padding:0}
html,body{width:1003px;height:1200px;overflow:hidden}
body{position:relative;background:var(--page);font-family:"Ubuntu",sans-serif;color:var(--ink)}
.abs{position:absolute}

.site-header{position:absolute;left:0;top:0;width:1003px;height:75px;background:var(--header);border-bottom:1px solid #d5d5d5}
.brand{position:absolute;left:92px;top:22px;display:flex;align-items:center;gap:6px;font:700 22px "Ubuntu",sans-serif;color:#2d4a6d}
.brand-dot{width:16px;height:16px;border-radius:50%;background:#f2b400}
.auth{position:absolute;left:654px;top:20px;display:flex;height:32px;border:1px solid #c8c8c8;border-radius:3px;overflow:hidden;background:#f4f4f4}
.auth a{display:flex;align-items:center;padding:0 15px;font-size:12px;color:#444;text-decoration:none;border-left:1px solid #cfcfcf}
.auth a.register{background:var(--red);color:#fff;border:none;padding:0 19px}

.hero{position:absolute;left:0;top:76px;width:1003px;height:437px;background:linear-gradient(180deg,#3aa7de 0%,#8fbfdc 30%,#7a8ea4 55%,#a67a6a 75%,#c98c6e 100%)}
.spot{position:absolute;border-radius:12px}
.spot .card{position:absolute;padding:10px 18px;color:#fff;font-size:12.5px;line-height:17px}
.spot .card h3{font-weight:400;font-size:14px;margin-bottom:3px}
.avatar{position:absolute;width:117px;height:117px;border-radius:50%;border:3px solid #fff;box-shadow:0 1px 4px rgba(0,0,0,.3)}

.cta{position:absolute;left:0;top:513px;width:1003px;height:91px;background:rgba(236,240,244,.92)}
.cta p{position:absolute;left:92px;top:14px;width:650px;font:400 25px/32px "Rokkitt",serif;color:#444}
.join{position:absolute;left:759px;top:25px;width:152px;height:41px;border-radius:3px;background:linear-gradient(#5ccdf5,var(--cyan));border:1px solid #1d9acb;color:#fff;font:500 24px/39px "Rokkitt",serif;text-align:center}

.features{position:absolute;left:0;top:604px;width:1003px;height:173px;background:var(--band)}
.feature{position:absolute;top:24px;width:240px;text-align:center}
.feature h2{font:500 19px "Rokkitt",serif;color:var(--blue);margin:6px 0 4px}
.feature p{font:300 11px/15px "Ubuntu",sans-serif;color:var(--muted)}
.feature svg{display:block;margin:0 auto}

.col{position:absolute;top:802px;width:242px}
.col-title{display:flex;align-items:center;gap:8px;font-size:16px;color:#444}
.col-title::after{content:"";flex:1;height:3px;border-top:1px solid var(--rule);border-bottom:1px solid var(--rule)}
.users{display:grid;grid-template-columns:repeat(4,48px);gap:10px 15px;margin-top:18px;margin-left:1px}
.users span{width:48px;height:47px;display:block}
.listing{display:flex;gap:10px;padding:6px 0 7px;border-bottom:1px solid #ddd}
.listing svg{flex:none;margin-top:6px}
.listing h4{font-weight:400;font-size:14px;color:#555}
.listing p{font:300 9.5px/12px "Ubuntu",sans-serif;color:var(--muted);margin-top:3px}
.media p{font:300 9px/12px "Ubuntu",sans-serif;color:#888;margin-top:9px}
.social-row{display:flex;align-items:center;gap:4px;margin-top:7px;font-size:8.5px;color:#444}
.pill{border:1px solid #c5cdd8;border-radius:3px;background:#f7f9fb;padding:2px 5px;font-size:8.5px;color:#3b5999}
.count{border:1px solid #ccc;border-radius:3px;padding:2px 4px;font-size:8px;background:#fff}
.sq{width:25px;height:25px;border-radius:4px;display:inline-block}

.site-footer{position:absolute;left:0;top:1082px;width:1003px;height:118px;background:var(--footer);color:var(--footer-text)}
.site-footer .copy{position:absolute;left:109px;top:14px;width:360px}
.site-footer .copy h5{font-weight:400;font-size:12.5px;color:#fff}
.site-footer .copy p{font:300 9px/12px "Ubuntu",sans-serif;margin-top:10px}
.fcol{position:absolute;top:15px}
.fcol h5{font-weight:500;font-size:12.5px;color:#fff;margin-bottom:10px}
.fcol a{display:block;font:300 9.5px/15px "Ubuntu",sans-serif;color:var(--footer-text);text-decoration:none}
</style>
</head>
<body>

<header class="site-header">
  <div class="brand"><span class="brand-dot"></span>LaneKindred.sg</div>
  <nav class="auth">
    <a class="register" href="#">Register</a>
    <a href="#">Login</a>
    <a href="#">Friendnet Login</a>
  </nav>
</header>

<section class="hero" role="img" aria-label="Blurred aerial photograph of the Singapore city skyline at dusk">
  <div class="spot" style="left:92px;top:90px">
    <div class="card" style="left:100px;top:10px;width:407px;height:76px;background:var(--blue-card);border-radius:0 4px 4px 0">
      <h3>Guitar Enthusiast</h3>
      Aisha, a non-professional guitar enthusiast, will teach beginner guitar for only $5 per lesson
    </div>
    <div class="avatar" role="img" aria-label="Portrait photo of Aisha" style="left:0;top:0;background:linear-gradient(135deg,#6a4a3c,#c99a84)"></div>
  </div>
  <div class="spot" style="left:404px;top:224px">
    <div class="card" style="left:0;top:10px;width:400px;height:76px;background:var(--red-card);border-radius:4px 0 0 4px;padding-left:22px">
      <h3>Architecture</h3>
      Mei Ling, an architecture undergraduate, will design your home from only $200
    </div>
    <div class="avatar" role="img" aria-label="Portrait photo of Mei Ling" style="left:391px;top:0;background:linear-gradient(135deg,#8a4f36,#e2b59c)"></div>
  </div>
</section>

<section class="cta">
  <p>You can also contribute to your neighbourhood's services and items pool. Take a FREE listing today!</p>
  <a class="join">Join Now</a>
</section>

<section class="features">
  <div class="feature" style="left:108px">
    <svg width="44" height="46" viewBox="0 0 44 46"><circle cx="22" cy="12" r="11" fill="var(--blue)"/><path d="M2 46v-8c0-8 8-12 20-12s20 4 20 12v8z" fill="var(--blue)"/><path d="M22 28l-3 3 3 13 3-13z" fill="#fff"/></svg>
    <h2>Professional</h2>
    <p>Lorem ipsum dolor sit amet, consectetur adipisi-cing elit, sed do eiusmod tempor incididunt ut labore et dolore magna aliqua...</p>
  </div>
  <div class="feature" style="left:382px">
    <svg width="44" height="46" viewBox="0 0 44 46"><path d="M10 12a12 12 0 0 1 24 0z" fill="var(--blue)"/><circle cx="22" cy="16" r="9" fill="none" stroke="var(--blue)" stroke-width="2.5"/><path d="M3 46v-8c0-7 7-11 19-11s19 4 19 11v8z" fill="none" stroke="var(--blue)" stroke-width="2.5"/><path d="M14 30v16M30 30v16" stroke="var(--blue)" stroke-width="2.5"/></svg>
    <h2>Non-Professional</h2>
    <p>Lorem ipsum dolor sit amet, consectetur adipisi-cing elit, sed do eiusmod tempor incididunt ut labore et dolore magna aliqua...</p>
  </div>
  <div class="feature" style="left:655px">
    <svg width="46" height="46" viewBox="0 0 46 46"><path d="M36 9L10 23l26 14" stroke="var(--blue)" stroke-width="5" fill="none"/><circle cx="36" cy="9" r="8" fill="var(--blue)"/><circle cx="10" cy="23" r="8" fill="var(--blue)"/><circle cx="36" cy="37" r="8" fill="var(--blue)"/></svg>
    <h2 style="margin-top:8px">Share And Help</h2>
    <p>Lorem ipsum dolor sit amet, consectetur adipisi-cing elit, sed do eiusmod tempor incididunt ut labore et dolore magna aliqua...</p>
  </div>
</section>

<section class="col" style="left:107px">
  <h3 class="col-title" style="font-weight:400">Latest Registered Users</h3>
  <div class="users" role="img" aria-label="Grid of sixteen member profile photos">
    <span style="background:#3b4a7a"></span><span style="background:#8a3a3a"></span><span style="background:#8aa0b0"></span><span style="background:#b08a6a"></span>
    <span style="background:#c08a50"></span><span style="background:#b8a090"></span><span style="background:#6a9ac8"></span><span style="background:#a0604a"></span>
    <span style="background:#e0a040"></span><span style="background:#7a6a7a"></span><span style="background:#9a8a6a"></span><span style="background:#c0b8a8"></span>
    <span style="background:#50a8d0"></span><span style="background:#6a5048"></span><span style="background:#8a6048"></span><span style="background:#b8a898"></span>
  </div>
</section>

<section class="col" style="left:380px">
  <h3 class="col-title" style="font-weight:400">Latest Listing</h3>
  <div style="margin-top:10px;margin-left:2px">
    <div class="listing">
      <svg width="36" height="30" viewBox="0 0 36 30"><rect x="12" y="10" width="16" height="18" rx="2" fill="#9a9a9a"/><path d="M12 14L2 6" stroke="#9a9a9a" stroke-width="3"/><path d="M28 12a6 6 0 0 1 0 10" stroke="#9a9a9a" stroke-width="2" fill="none"/></svg>
      <div><h4>Water Plants While Away</h4><p>Ben Tan wants to offer I can help water your plants while you're overseas! I'm dependable and detailed..</p></div>
    </div>
    <div class="listing">
      <svg width="36" height="30" viewBox="0 0 36 30"><path d="M22 1L10 17h8l-4 13 12-17h-8z" fill="#9a9a9a"/></svg>
      <div><h4>Electricity Repair (DIY)</h4><p>KTW wants to offer Electrical Repair (DIY)</p></div>
    </div>
    <div class="listing">
      <svg width="36" height="30" viewBox="0 0 36 30"><rect x="2" y="4" width="22" height="9" rx="2" fill="#9a9a9a"/><rect x="24" y="7" width="9" height="3" fill="#9a9a9a"/><rect x="6" y="13" width="7" height="14" rx="1" fill="#9a9a9a"/></svg>
      <div><h4>Driling</h4><p>FarisK has shared Electric Drill</p></div>
    </div>
    <div class="listing">
      <svg width="36" height="30" viewBox="0 0 36 30"><rect x="3" y="12" width="14" height="14" rx="3" fill="#9a9a9a"/><rect x="19" y="8" width="12" height="16" rx="3" fill="#9a9a9a"/><path d="M24 8V2M27 8V2" stroke="#9a9a9a" stroke-width="2"/></svg>
      <div><h4>Travel Acessories</h4><p>JasonL is selling Micro/Nano Sim Adapters</p></div>
    </div>
  </div>
</section>

<section class="col media" style="left:654px">
  <h3 class="col-title" style="font-weight:400">Media Mention</h3>
  <p style="margin-top:14px">LaneKindred.sg is an initiative supported by CNVH.</p>
  <p>“LaneKindred.sg fills a critical gap, by providing a mechanism for neighbours to communicate with each other their resources and their willingness to help.”<br>- NMP Darren Oei, CEO of CNVH</p>
  <h3 class="col-title" style="font-weight:400;margin-top:12px">Follow Us</h3>
  <div class="social-row" style="margin-top:9px"><span class="pill">Like</span><span class="sq" style="width:9px;height:9px;border-radius:1px;background:#3b5999;align-self:flex-start"></span><span style="width:150px;line-height:11px">Be the first of your friends to like this.</span></div>
  <div class="social-row"><span class="pill">Post</span><span class="count">0</span></div>
  <div class="social-row"><span class="pill">Follow @sitecraft</span><span class="count">169K followers</span></div>
  <div class="social-row" style="gap:5px;margin-top:8px"><span class="sq" style="background:#3b5a9a"></span><span class="sq" style="background:#35b2e8"></span><span class="sq" style="background:#d8402f"></span></div>
</section>

<footer class="site-footer">
  <div class="copy">
    <h5>© Harbourlane Pte LTD 2013</h5>
    <p>LaneKindred.sg is an initiative supported by CNVH.</p>
    <p>“LaneKindred.sg fills a critical gap, by providing a mechanism for neighbours to communicate with each other their resources and their willingness to help.”<br>- NMP Darren Oei, CEO of CNVH</p>
  </div>
  <div class="fcol" style="left:535px"><h5>Want to know more?</h5><a href="#">About Us</a><a href="#">FAQ</a></div>
  <div class="fcol" style="left:681px"><h5>Using Lane Kindred</h5><a href="#">Terms of use</a><a href="#">Privacy Policy</a></div>
  <div class="fcol" style="left:824px"><h5>Get in touch</h5><a href="#">Contact Us</a><a href="#">Friendnet</a></div>
</footer>

</body>
</html>
```